Brimsett Gardening Fresh New Website

We are looking to create a simple fresh website for our landscaping business. The website should appeal to a 'high end' audience. We deal with a lot of Embassies and affluent clients who have extremely large gardens that are meticulously maintained. The site is about communicating our excellent landscaping and customer service skills and encouraging new clients to reach out and engage us to take care of their gardens.

The website is basically going to be our business card, it will have almost no functionality other than two 'contact us' forms, one for smaller clients and one for more detailed projects.

The website will not have a lot of written content and will have to show photos of beautifully landscaped gardens.

The main logo in black will influence the site, however, we are open to all suggestions.

We are expecting to have the following pages:
Home Page
Services
About Us
Contact Us
Showcase (photo gallery of our work)

We need someone who can code it to wordpress and be available for minor changes over a number of days. They will be simple tweaks.

```html
<!DOCTYPE html>
<html lang="en">
<head>
<meta charset="utf-8">
<title>Brimsett Gardening</title>
<link href="https://fonts.googleapis.com/css2?family=Tinos:ital,wght@0,400;0,700;1,400&family=Poppins:wght@400;500&family=Montserrat:wght@600;700&display=swap" rel="stylesheet">
<style>
:root{
  --gold:#d4a72c;
  --gold-text:#c79a2e;
  --ink:#1d1d1d;
  --paper:#ffffff;
  --mist:#f4f4f4;
  --night:#0d0d0d;
  --gold-grad:linear-gradient(90deg,#9c721b 0%,#e6bf45 50%,#a67a1e 100%);
}
*{box-sizing:border-box;margin:0;padding:0}
html,body{width:1200px;height:4329px;overflow:hidden}
body{position:relative;background:var(--paper);font-family:"Poppins",sans-serif;color:var(--ink)}
.abs{position:absolute}
.serif{font-family:"Tinos",serif}
.btn{position:absolute;display:flex;align-items:center;justify-content:center;border-radius:30px;background:var(--gold-grad);color:#1a1205;font-family:"Montserrat",sans-serif;font-weight:700;font-size:16px}
.field{position:absolute;border:1px solid #555;border-radius:24px;background:#fff;font-size:13px;color:#222;padding:0 18px;display:flex;align-items:center}

/* hero */
.hero{left:0;top:0;width:1200px;height:682px;background:
  radial-gradient(ellipse 260px 520px at 560px 620px,rgba(120,118,110,.95),rgba(120,118,110,0) 70%),
  radial-gradient(ellipse 340px 160px at 420px 430px,rgba(150,150,140,.55),rgba(150,150,140,0) 70%),
  radial-gradient(ellipse 520px 260px at 250px 300px,#6f9a2e,rgba(111,154,46,0) 75%),
  radial-gradient(ellipse 300px 220px at 1110px 480px,#2f4a1f,rgba(47,74,31,0) 75%),
  radial-gradient(ellipse 420px 120px at 600px 40px,#6a6c66,rgba(106,108,102,0) 75%),
  linear-gradient(180deg,#3f4a38 0%,#4f6b2a 18%,#6a922c 40%,#5a7f26 62%,#5e5f56 85%,#45443e 100%)}
.hero-shade{left:0;top:0;width:1200px;height:682px;background:linear-gradient(90deg,rgba(0,0,0,.42),rgba(0,0,0,.08) 60%,rgba(0,0,0,.22)),linear-gradient(180deg,rgba(0,0,0,.35),rgba(0,0,0,0) 22%)}
.brand{left:60px;top:82px;width:164px;text-align:center;color:#fff;font-family:"Tinos",serif}
.brand .mark{width:14px;height:14px;border-radius:50%;background:#fff;margin:0 auto 12px}
.brand .name{font-size:20px;letter-spacing:7px}
.brand .sub{font-size:10px;letter-spacing:6px;margin-top:2px}
.nav{left:360px;top:62px;display:flex;gap:26px;font-family:"Tinos",serif;font-size:15px;color:#fff}
.nav .active{border-bottom:1px solid #fff;padding-bottom:6px}
.phone-pill{left:886px;top:47px;width:240px;height:45px;font-family:"Tinos",serif;font-size:25px;color:#fff;gap:8px}
.hero-title{left:74px;top:278px;font-size:56px;color:#fff;letter-spacing:1px;font-weight:700}
.hero-sub{left:74px;top:346px;width:560px;font-size:30px;line-height:38px;color:#fff;font-weight:500}
.quick{left:795px;top:166px;width:331px;height:447px;border:1px solid rgba(255,255,255,.4);border-radius:8px;background:rgba(0,0,0,.35)}
.quick h3{position:absolute;left:0;top:28px;width:100%;text-align:center;font-family:"Tinos",serif;font-weight:400;font-size:32px;color:#fff}

/* services */
.section-title{left:0;width:1200px;text-align:center;font-family:"Tinos",serif;font-size:40px;font-weight:400;color:var(--ink)}
.card{width:329px;height:339px;overflow:hidden}
.card .shot{position:absolute;inset:0}
.card .fade{position:absolute;inset:0;background:linear-gradient(180deg,rgba(0,0,0,0) 45%,rgba(0,0,0,.95) 88%)}
.card .label{position:absolute;left:0;top:224px;width:100%;text-align:center;font-family:"Tinos",serif;font-size:31px;color:#fff}
.card .btn{left:97px;top:275px;width:135px;height:44px;font-size:15px}

/* welcome */
.welcome-bg{left:0;top:1249px;width:1200px;height:730px}
.frame-dark{left:74px;top:1326px;width:423px;height:442px;background:#222}
.frame-gold{left:466px;top:1680px;width:137px;height:191px;background:#f1cf3a}
.team-photo{left:92px;top:1345px;width:495px;height:505px;background:
  radial-gradient(ellipse 90px 200px at 140px 330px,rgba(190,150,110,.8),rgba(190,150,110,0) 75%),
  radial-gradient(ellipse 80px 190px at 250px 300px,rgba(70,80,110,.75),rgba(70,80,110,0) 75%),
  radial-gradient(ellipse 140px 90px at 210px 230px,rgba(40,90,200,.25),rgba(40,90,200,0) 75%),
  radial-gradient(ellipse 220px 90px at 220px 60px,rgba(130,170,120,.6),rgba(130,170,120,0) 75%),
  linear-gradient(135deg,#eceee8,#d6d9d0 50%,#b8bdb3)}
.welcome-h{left:617px;top:1400px;font-size:40px;line-height:44px;font-weight:400;color:var(--ink)}
.welcome-tag{left:617px;top:1498px;font-family:"Tinos",serif;font-style:italic;font-size:25px;color:var(--gold-text)}
.welcome-copy{left:617px;top:1542px;width:512px;font-size:14.2px;line-height:28px;color:#555}

/* testimonials */
.testi-bg{left:0;top:2874px;width:1200px;height:690px}
.t-card{background:#fff;text-align:center;padding:0 24px}
.avatar{width:100px;height:100px;border-radius:50%;margin:0 auto}
.t-card p{font-size:14px;line-height:22.5px;color:#333}
.t-card .who{font-family:"Tinos",serif;font-weight:700;font-size:18px;color:var(--gold-text);margin-top:6px}

/* contact */
.contact-h{left:72px;top:3630px;font-size:40px;font-weight:400}
.contact-lead{left:72px;top:3684px;width:540px;font-size:14.5px;line-height:24px;color:#333}
.select-arrow{margin-left:auto;font-size:8px;line-height:8px;text-align:center}
.address{left:615px;top:3639px;width:511px;height:433px;border-radius:10px;background:radial-gradient(ellipse 260px 160px at 420px 360px,rgba(60,70,40,.55),rgba(60,70,40,0) 75%),linear-gradient(160deg,#1b1b1b,#0b0b0b 60%,#1a1c16);color:#fff}
.address h3{position:absolute;left:32px;top:34px;font-family:"Tinos",serif;font-weight:400;font-size:40px}
.addr-row{position:absolute;left:32px;display:flex;align-items:center;gap:22px;font-size:14.5px;line-height:22px}
.dot{width:37px;height:37px;border-radius:50%;background:var(--gold-grad);display:flex;align-items:center;justify-content:center;flex:none}
.follow{position:absolute;left:32px;top:298px;font-family:"Tinos",serif;font-size:24px}
.socials{position:absolute;left:32px;top:352px;display:flex;gap:17px}
.socials span{width:18px;height:18px;border-radius:50%;background:var(--gold)}
.addr-brand{position:absolute;left:315px;top:170px;width:180px;text-align:center;color:var(--gold);font-family:"Tinos",serif}
.addr-brand .name{font-size:20px;letter-spacing:6px}
.addr-brand .sub{font-size:11px;letter-spacing:5px;margin-top:4px}
.addr-brand .mark{width:14px;height:14px;border-radius:50%;background:var(--gold);margin:0 auto 14px}

/* footer */
.footer{left:0;top:4151px;width:1200px;height:178px;background:var(--night);color:#fff}
.footer-nav{position:absolute;left:0;top:48px;width:100%;display:flex;justify-content:center;gap:40px;font-family:"Tinos",serif;font-size:24px}
.footer-copy{position:absolute;left:0;top:104px;width:100%;text-align:center;font-size:13px}
</style>
</head>
<body>

<!-- Hero -->
<div class="abs hero" role="img" aria-label="Manicured lawn with curving paved garden path beside a large house"></div>
<div class="abs hero-shade"></div>
<div class="abs brand"><div class="mark"></div><div class="name">BRIMSETT</div><div class="sub">GARDENING</div></div>
<nav class="abs nav"><span class="active">HOME</span><span>ABOUT</span><span>OUR SERVICES</span><span>SHOWCASE</span><span>CONTACT</span></nav>
<div class="btn phone-pill">
  <svg width="20" height="20" viewBox="0 0 24 24" fill="#fff"><path d="M6.6 10.8a15.1 15.1 0 0 0 6.6 6.6l2.2-2.2c.3-.3.7-.4 1-.2 1.1.4 2.3.6 3.6.6.6 0 1 .4 1 1V20c0 .6-.4 1-1 1A17 17 0 0 1 3 4c0-.6.4-1 1-1h3.5c.6 0 1 .4 1 1 0 1.3.2 2.5.6 3.6.1.3 0 .7-.2 1z"/></svg>
  +188-555-0142
</div>
<h1 class="abs serif hero-title">BRIMSETT GARDENING</h1>
<p class="abs hero-sub">Excepteur sint occaecat cupidatat non proident laboris nisi.</p>
<div class="btn" style="left:77px;top:444px;width:182px;height:47px;font-size:18px;font-weight:600">Read More</div>

<div class="abs quick">
  <h3>QUICK CONTACT</h3>
  <div class="field" style="left:10px;top:83px;width:309px;height:45px">First Name</div>
  <div class="field" style="left:10px;top:140px;width:309px;height:45px">Email Address</div>
  <div class="field" style="left:10px;top:197px;width:309px;height:45px">Phone No</div>
  <div class="field" style="left:10px;top:254px;width:309px;height:104px;align-items:flex-start;padding-top:12px;border-radius:12px">Message</div>
  <div class="btn" style="left:42px;top:375px;width:247px;height:46px;font-size:19px">Submit</div>
</div>

<!-- Services -->
<h2 class="abs section-title" style="top:738px">SERVICE WE OFFERS</h2>
<div class="abs card" style="left:74px;top:824px">
  <div class="shot" role="img" aria-label="Hand colouring a landscape garden plan" style="background:radial-gradient(ellipse 90px 70px at 90px 60px,rgba(150,190,110,.8),rgba(150,190,110,0) 75%),radial-gradient(ellipse 120px 70px at 160px 150px,rgba(90,150,190,.75),rgba(90,150,190,0) 75%),radial-gradient(ellipse 70px 110px at 290px 140px,rgba(235,190,160,.9),rgba(235,190,160,0) 75%),radial-gradient(ellipse 110px 80px at 260px 30px,rgba(240,240,235,.9),rgba(240,240,235,0) 75%),linear-gradient(140deg,#dfe6cf,#c7d6c0 50%,#b3c3c0)"></div>
  <div class="fade"></div><div class="label">EXCEPTEUR</div><div class="btn">Read More</div>
</div>
<div class="abs card" style="left:437px;top:824px">
  <div class="shot" role="img" aria-label="Gardener laying turf beside a brick path" style="background:radial-gradient(ellipse 60px 90px at 200px 120px,rgba(40,110,90,.85),rgba(40,110,90,0) 75%),radial-gradient(ellipse 130px 70px at 250px 200px,rgba(170,110,110,.8),rgba(170,110,110,0) 75%),radial-gradient(ellipse 120px 60px at 90px 200px,rgba(90,140,60,.8),rgba(90,140,60,0) 75%),linear-gradient(180deg,#4a3026 0%,#5d3e30 35%,#6f5a4a 60%,#54463a)"></div>
  <div class="fade"></div><div class="label">EXCEPTEUR</div><div class="btn">Read More</div>
</div>
<div class="abs card" style="left:798px;top:824px">
  <div class="shot" role="img" aria-label="Lawn with young trees under a blue sky" style="background:radial-gradient(ellipse 70px 60px at 110px 120px,rgba(60,110,40,.95),rgba(60,110,40,0) 75%),radial-gradient(ellipse 60px 70px at 270px 110px,rgba(40,90,40,.95),rgba(40,90,40,0) 75%),radial-gradient(ellipse 200px 40px at 165px 60px,rgba(255,255,255,.5),rgba(255,255,255,0) 75%),linear-gradient(180deg,#3f8fdc 0%,#8ec4ea 38%,#5d9a3a 52%,#6fae35 70%,#3d6b24)"></div>
  <div class="fade"></div><div class="label">EXCEPTEUR</div><div class="btn">Read More</div>
</div>

<!-- Welcome -->
<svg class="abs welcome-bg" viewBox="0 0 1200 730" width="1200" height="730" aria-hidden="true">
  <defs><linearGradient id="goldBand" x1="0" x2="1"><stop offset="0" stop-color="#9c721b"/><stop offset=".5" stop-color="#ecc652"/><stop offset="1" stop-color="#9c721b"/></linearGradient></defs>
  <rect x="0" y="0" width="1200" height="730" fill="#f4f4f4"/>
  <polygon points="0,650 600,722 1200,650 1200,676 600,728 0,676" fill="url(#goldBand)"/>
  <polygon points="0,676 600,728 1200,676 1200,730 0,730" fill="#fff"/>
</svg>
<div class="abs frame-dark"></div>
<div class="abs frame-gold"></div>
<div class="abs team-photo" role="img" aria-label="Designers presenting a garden plan to an applauding team"></div>
<h2 class="abs serif welcome-h">WELCOME TO<br>BRIMSETT GARDENING</h2>
<p class="abs welcome-tag">Excepteur sint occaecat cupidatat non proident</p>
<p class="abs welcome-copy">Sed ut perspiciatis unde omnis iste natus error sit voluptatem accusantium doloremque laudantium, totam rem aperiam, eaque ipsa quae ab illo inventore veritatis et quasi architecto beatae vitae dicta sunt explicabo. Nemo enim ipsam voluptatem quia voluptas sit aspernatur aut odit aut fugit, sed quia consequuntur magni dolores eos qui ratione voluptatem sequi nesciunt.</p>
<div class="btn" style="left:617px;top:1741px;width:134px;height:45px;font-size:15px">Read More</div>

<!-- Showcase -->
<h2 class="abs section-title" style="top:2035px">SHOWCASE</h2>
<div class="abs" style="left:74px;top:2126px;width:521px;height:279px;background:radial-gradient(ellipse 70px 80px at 400px 120px,rgba(40,45,50,.95),rgba(40,45,50,0) 75%),radial-gradient(ellipse 80px 120px at 60px 110px,rgba(180,120,70,.9),rgba(180,120,70,0) 75%),radial-gradient(ellipse 200px 50px at 360px 230px,rgba(110,170,40,.95),rgba(110,170,40,0) 75%),radial-gradient(ellipse 140px 40px at 180px 250px,rgba(170,170,165,.85),rgba(170,170,165,0) 75%),linear-gradient(180deg,#7f958a 0%,#4f5e38 35%,#5c7a30 70%,#8a8f84)" role="img" aria-label="Garden studio with timber fence and lawn"></div>
<div class="abs" style="left:607px;top:2126px;width:254px;height:279px;background:radial-gradient(ellipse 120px 40px at 130px 90px,rgba(130,190,60,.95),rgba(130,190,60,0) 75%),radial-gradient(ellipse 90px 60px at 60px 170px,rgba(160,90,140,.85),rgba(160,90,140,0) 75%),radial-gradient(ellipse 140px 60px at 180px 250px,rgba(215,160,120,.95),rgba(215,160,120,0) 75%),linear-gradient(180deg,#8cbce0 0%,#4f7d34 22%,#6a9a3a 45%,#7a6a5a 70%,#c99b78)" role="img" aria-label="Flower border beside a herringbone brick path"></div>
<div class="abs" style="left:872px;top:2126px;width:254px;height:279px;background:radial-gradient(ellipse 60px 60px at 60px 30px,rgba(170,80,50,.95),rgba(170,80,50,0) 75%),radial-gradient(ellipse 70px 50px at 210px 110px,rgba(230,110,40,.85),rgba(230,110,40,0) 75%),radial-gradient(ellipse 90px 50px at 60px 230px,rgba(70,80,180,.85),rgba(70,80,180,0) 75%),radial-gradient(ellipse 90px 120px at 110px 150px,rgba(160,160,165,.85),rgba(160,160,165,0) 75%),linear-gradient(170deg,#6a7a5a,#5a8a3a 40%,#6a7a40 70%,#4a5a30)" role="img" aria-label="Colourful flower beds along a paved path"></div>
<div class="abs" style="left:74px;top:2415px;width:255px;height:279px;background:radial-gradient(ellipse 70px 60px at 40px 90px,rgba(190,50,40,.9),rgba(190,50,40,0) 75%),radial-gradient(ellipse 90px 70px at 170px 80px,rgba(110,150,50,.9),rgba(110,150,50,0) 75%),radial-gradient(ellipse 90px 60px at 130px 200px,rgba(170,200,215,.9),rgba(170,200,215,0) 75%),linear-gradient(175deg,#7a8a40,#6a5a30 40%,#8a8070 65%,#3a3a30)" role="img" aria-label="Stone water feature with planting"></div>
<div class="abs" style="left:340px;top:2415px;width:255px;height:279px;background:radial-gradient(ellipse 60px 40px at 80px 100px,rgba(220,180,120,.7),rgba(220,180,120,0) 75%),radial-gradient(ellipse 70px 40px at 130px 210px,rgba(160,230,90,.8),rgba(160,230,90,0) 75%),linear-gradient(180deg,#141c22,#26343a 40%,#1e4a22 70%,#133017)" role="img" aria-label="Lit modern garden at dusk"></div>
<div class="abs" style="left:607px;top:2415px;width:519px;height:279px;background:radial-gradient(ellipse 60px 90px at 120px 90px,rgba(40,80,30,.95),rgba(40,80,30,0) 75%),radial-gradient(ellipse 80px 90px at 330px 80px,rgba(90,130,50,.9),rgba(90,130,50,0) 75%),radial-gradient(ellipse 220px 50px at 230px 200px,rgba(140,200,40,.95),rgba(140,200,40,0) 75%),radial-gradient(ellipse 80px 80px at 470px 230px,rgba(150,150,145,.85),rgba(150,150,145,0) 75%),linear-gradient(180deg,#9a8a70,#4a6a2a 30%,#6f9a30 60%,#5a6a3a)" role="img" aria-label="Large lawn with clipped shrubs and patio"></div>
<div class="btn" style="left:519px;top:2746px;width:178px;height:47px;font-size:15px">View All</div>

<!-- Testimonials -->
<svg class="abs testi-bg" viewBox="0 0 1200 690" width="1200" height="690" aria-hidden="true">
  <defs>
    <linearGradient id="goldBand2" x1="0" x2="1"><stop offset="0" stop-color="#9c721b"/><stop offset=".5" stop-color="#ecc652"/><stop offset="1" stop-color="#9c721b"/></linearGradient>
    <linearGradient id="night" x1="0" y1="0" x2="0" y2="1"><stop offset="0" stop-color="#1a1f16"/><stop offset=".5" stop-color="#26301e"/><stop offset="1" stop-color="#1a2016"/></linearGradient>
    <radialGradient id="shrub" cx=".15" cy=".55" r=".35"><stop offset="0" stop-color="#4a4a5a" stop-opacity=".7"/><stop offset="1" stop-color="#4a4a5a" stop-opacity="0"/></radialGradient>
    <radialGradient id="path" cx=".75" cy=".85" r=".3"><stop offset="0" stop-color="#6a6a64" stop-opacity=".6"/><stop offset="1" stop-color="#6a6a64" stop-opacity="0"/></radialGradient>
  </defs>
  <g role="img" aria-label="Evening garden with shrubs and a paved path">
    <polygon points="0,80 600,10 1200,80 1200,613 600,689 0,613" fill="url(#night)"/>
    <polygon points="0,80 600,10 1200,80 1200,613 600,689 0,613" fill="url(#shrub)"/>
    <polygon points="0,80 600,10 1200,80 1200,613 600,689 0,613" fill="url(#path)"/>
  </g>
  <polygon points="0,60 600,0 1200,60 1200,80 600,14 0,80" fill="url(#goldBand2)"/>
  <polygon points="0,605 600,672 1200,605 1200,625 600,690 0,625" fill="url(#goldBand2)"/>
</svg>
<h2 class="abs section-title" style="top:3003px;color:#fff">TESTIMONIALS</h2>
<div class="abs t-card" style="left:74px;top:3116px;width:329px;height:296px;padding-top:32px">
  <div class="avatar" role="img" aria-label="Portrait of a smiling couple" style="background:radial-gradient(circle at 35% 45%,#8a5a3a,rgba(138,90,58,0) 45%),radial-gradient(circle at 65% 50%,#4a2e22,rgba(74,46,34,0) 45%),#c8ccd4"></div>
  <p style="margin-top:28px">" Nemo enim ipsam voluptatem quia voluptas sit aspernatur aut odit aut fugit, sed quia consequuntur.."</p>
  <div class="who">Name Heading</div>
</div>
<div class="abs t-card" style="left:437px;top:3099px;width:329px;height:330px;padding-top:18px">
  <div class="avatar" role="img" aria-label="Portrait of a smiling couple" style="background:radial-gradient(circle at 35% 50%,#5a3a2a,rgba(90,58,42,0) 45%),radial-gradient(circle at 65% 55%,#8a6a4a,rgba(138,106,74,0) 45%),#d9a820"></div>
  <p style="margin-top:24px">" Nemo enim ipsam voluptatem quia voluptas sit aspernatur aut odit aut fugit, sed quia consequuntur sint occaecat cupidatat non proident, sunt in culpa qui officia deserunt mollit anim id est laborum."</p>
  <div class="who">Name Heading</div>
</div>
<div class="abs t-card" style="left:798px;top:3116px;width:329px;height:296px;padding-top:32px">
  <div class="avatar" role="img" aria-label="Portrait of a smiling man" style="background:radial-gradient(circle at 50% 50%,#6a4030,rgba(106,64,48,0) 50%),#8ab4d6"></div>
  <p style="margin-top:28px">" Nemo enim ipsam voluptatem quia voluptas sit aspernatur aut odit aut fugit, sed quia consequuntur.."</p>
  <div class="who">Name Heading</div>
</div>

<!-- Contact -->
<h2 class="abs serif contact-h">CONTACT US</h2>
<p class="abs contact-lead">Please fill out a contact form and we will follow up with you and your unique project needs.</p>
<div class="field" style="left:74px;top:3748px;width:249px;height:45px">First Name</div>
<div class="field" style="left:338px;top:3748px;width:249px;height:45px">Last Name</div>
<div class="field" style="left:74px;top:3805px;width:249px;height:45px">Email Address</div>
<div class="field" style="left:338px;top:3805px;width:249px;height:45px">Phone No</div>
<div class="field" style="left:74px;top:3861px;width:249px;height:45px">Select Services<span class="select-arrow">&#9650;<br>&#9660;</span></div>
<div class="field" style="left:338px;top:3861px;width:249px;height:45px">Select date
  <svg class="select-arrow" width="13" height="13" viewBox="0 0 14 14"><rect x="1" y="3" width="12" height="10" fill="#333"/><rect x="3" y="0" width="2" height="4" fill="#333"/><rect x="9" y="0" width="2" height="4" fill="#333"/></svg>
</div>
<div class="field" style="left:74px;top:3918px;width:513px;height:99px;align-items:flex-start;padding-top:14px;border-radius:14px">Message</div>
<div class="btn" style="left:74px;top:4029px;width:249px;height:45px;font-size:19px">Submit</div>

<div class="abs address" role="group" aria-label="Address">
  <h3>ADDRESS</h3>
  <div class="addr-row" style="top:98px">
    <span class="dot"><svg width="16" height="18" viewBox="0 0 24 24" fill="#1a1205"><path d="M12 2a7 7 0 0 0-7 7c0 5 7 13 7 13s7-8 7-13a7 7 0 0 0-7-7zm0 9.5A2.5 2.5 0 1 1 12 6a2.5 2.5 0 0 1 0 5.5z"/></svg></span>
    <span>48 Larkmoor Lane Suite 12,<br>Ashford 20415, United State</span>
  </div>
  <div class="addr-row" style="top:170px">
    <span class="dot"><svg width="16" height="16" viewBox="0 0 24 24" fill="#1a1205"><path d="M6.6 10.8a15.1 15.1 0 0 0 6.6 6.6l2.2-2.2c.3-.3.7-.4 1-.2 1.1.4 2.3.6 3.6.6.6 0 1 .4 1 1V20c0 .6-.4 1-1 1A17 17 0 0 1 3 4c0-.6.4-1 1-1h3.5c.6 0 1 .4 1 1 0 1.3.2 2.5.6 3.6.1.3 0 .7-.2 1z"/></svg></span>
    <span>+188-555-0142</span>
  </div>
  <div class="addr-row" style="top:226px">
    <span class="dot"><svg width="16" height="14" viewBox="0 0 24 20" fill="none" stroke="#1a1205" stroke-width="2.2"><rect x="2" y="2" width="20" height="16" rx="2"/><path d="M2 4l10 7 10-7"/></svg></span>
    <span>hello@brimsettgardening.com</span>
  </div>
  <div class="follow">FOLLOW US</div>
  <div class="socials" aria-label="Social links"><span></span><span></span><span></span><span></span><span></span></div>
  <div class="addr-brand"><div class="mark"></div><div class="name">BRIMSETT</div><div class="sub">GARDENING</div></div>
</div>

<!-- Footer -->
<footer class="abs footer">
  <nav class="footer-nav"><span>Home</span><span>About</span><span>Our Services</span><span>Showcase</span><span>Contact</span></nav>
  <p class="footer-copy">Copyright © 2024. Company Name All Right Reserved. Privacy Policy</p>
</footer>

</body>
</html>
```